Private Investigation Business Card Design

I need a business card for a new private investigation company named Brisk Inquiries. I perform mainly surveillance jobs, vehicle repossessions, document serves etc. The final design should aim for a professional look. The logo has a magnifying glass with stick man arms and legs and is in a running action to show the "Brisk" aspect of the name. If the colour scheme could remain the same as the website www.briskinquiries-demo.com.au with silvers,blacks and a couple electric blue highlights.
Industry/Entity Type
Business
Contact Information for Business Card
Morgan Kellaway
Brisk Inquiries
0487316204
PO Box 58, Carnwell NSW 2291
info@briskinquiries-demo.com.au
www.briskinquiries-demo.com.au
Look and feel

```html
<!DOCTYPE html>
<html lang="en">
<head>
<meta charset="utf-8">
<title>Brisk Inquiries – Business Card</title>
<link href="https://fonts.googleapis.com/css2?family=Open+Sans:ital,wght@0,400;0,600;1,400&display=swap" rel="stylesheet">
<style>
  :root {
    --stage: #e6e6e6;
    --card-front: #ffffff;
    --card-back-light: #c9c9c9;
    --card-back-dark: #8f8f8f;
    --ink: #2b2b2b;
    --ink-soft: #4a4a4a;
    --silver-light: #f2f2f2;
    --silver-mid: #b5b5b5;
    --silver-dark: #7a7a7a;
  }
  * { box-sizing: border-box; margin: 0; padding: 0; }
  html, body { width: 1200px; height: 750px; overflow: hidden; }
  body {
    background: var(--stage);
    font-family: "Open Sans", sans-serif;
    color: var(--ink);
    position: relative;
  }
  .card {
    position: absolute;
    top: 228px;
    width: 461px;
    height: 263px;
    overflow: hidden;
  }
  .card--front { left: 124px; background: var(--card-front); }
  .card--back {
    left: 618px;
    background: radial-gradient(circle at 45% 40%, var(--card-back-light) 0%, #b0b0b0 55%, var(--card-back-dark) 100%);
  }

  .brand {
    position: absolute;
    display: flex;
    align-items: center;
    gap: 8px;
    font-weight: 600;
    font-size: 22px;
    line-height: 1;
    letter-spacing: 0.3px;
    color: var(--ink);
    white-space: nowrap;
  }
  .brand__dot {
    width: 11px; height: 11px; border-radius: 50%;
    background: var(--silver-dark);
    flex: none;
  }
  .card--front .brand { left: 38px; top: 48px; }
  .card--back .brand { left: 36px; top: 198px; }

  .address {
    position: absolute; left: 38px; top: 150px;
    font-size: 11px; line-height: 14px; color: var(--ink-soft);
  }
  .contact-list {
    position: absolute; left: 38px; top: 183px;
    list-style: none; font-size: 11px; color: var(--ink-soft);
  }
  .contact-list li {
    display: flex; align-items: center; gap: 7px;
    height: 17.5px;
  }
  .contact-list svg { width: 11px; height: 11px; fill: var(--ink); flex: none; }

  .name-band {
    position: absolute; left: 294px; top: 138px;
    width: 167px; height: 44px;
    background: linear-gradient(to bottom, var(--silver-light) 0%, #d6d6d6 45%, var(--silver-mid) 100%);
    border-radius: 4px 0 0 4px;
    display: flex; align-items: center;
    padding-left: 18px;
    font-size: 16px; font-weight: 600; color: var(--ink);
    white-space: nowrap;
  }
  .runner-mini {
    position: absolute; left: 258px; top: 140px;
    width: 34px; height: 40px;
    background: linear-gradient(135deg, #d0d0d0, #6a6a6a);
    border-radius: 4px;
  }

  .runner-art {
    position: absolute; left: 244px; top: 18px;
    width: 210px; height: 228px;
    background: radial-gradient(ellipse at 60% 45%, #9c9c9c 0%, #5a5a5a 70%, #3a3a3a 100%);
    border-radius: 8px;
    opacity: 0.85;
  }
  .web {
    position: absolute; left: 36px; top: 228px;
    font-size: 10.5px; font-style: italic; color: var(--ink);
    white-space: nowrap;
  }
</style>
</head>
<body>
  <section class="card card--front" aria-label="Business card front">
    <div class="brand"><span class="brand__dot"></span>Brisk Inquiries</div>

    <p class="address">PO Box 58<br>Carnwell NSW 2291</p>

    <ul class="contact-list">
      <li>
        <svg viewBox="0 0 24 24" aria-hidden="true"><path d="M6.6 10.8a15.1 15.1 0 0 0 6.6 6.6l2.2-2.2c.3-.3.7-.4 1-.2 1.1.4 2.3.6 3.6.6.6 0 1 .4 1 1V20c0 .6-.4 1-1 1C10.6 21 3 13.4 3 4c0-.6.4-1 1-1h3.5c.6 0 1 .4 1 1 0 1.3.2 2.5.6 3.6.1.3 0 .7-.2 1z"/></svg>
        0487 316 204
      </li>
      <li>
        <svg viewBox="0 0 24 24" aria-hidden="true"><path d="M2 5h20v14H2z M3.5 6.5l8.5 6 8.5-6" fill="none" stroke="#2b2b2b" stroke-width="2.4"/></svg>
        info@briskinquiries-demo.com.au
      </li>
      <li>
        <svg viewBox="0 0 24 24" aria-hidden="true"><circle cx="12" cy="12" r="10"/><path d="M2 12h20M12 2c3 3 3 17 0 20M12 2c-3 3-3 17 0 20" fill="none" stroke="#fff" stroke-width="1.4"/></svg>
        www.briskinquiries-demo.com.au
      </li>
    </ul>

    <div class="runner-mini" role="img" aria-label="Small running magnifying-glass figure"></div>
    <div class="name-band">Morgan Kellaway</div>
  </section>

  <section class="card card--back" aria-label="Business card back">
    <div class="runner-art" role="img" aria-label="Large illustration of a running magnifying-glass figure with speed lines"></div>
    <div class="brand"><span class="brand__dot"></span>Brisk Inquiries</div>
    <p class="web">www.briskinquiries-demo.com.au</p>
  </section>
</body>
</html>
```